Tinker's Lamp sports bar beer & food menu

We need a menu design for our gastropub sports bar in L.A.'s Sawtelle Neighborhood (Little Osaka). We have a full-bar (hard liquor, craft beer, wine and cocktails) . We have a lunch and dinner menu as well as a happy hour menu. On Sundays we have a seperate menu with brunch items. The design concept is a British pub type of sports bar. We're looking for something different from our existing menu design. Ideally something cleaner and more legible. It should mesh a simple, modern sensibility with the more traditional darkened pub style of our interior design.

You can check out our Voxly page for photos of the interior/exterior:
https://www.reviewhatch.example/biz_photos/tinkers-lamp-los-angeles?tab=interior

You can view our existing menu here:
https://www.reviewhatch.example/biz_photos/tinkers-lamp-los-angeles?tab=menu

If there's an area of the design that can be a little more playful it's our highlighted event schedule so that the events will stand out.

Target Market(s)

Age of 25 and up. Sawtelle is a cultural hub that caters to a younger, moderately affluent crowd.

Industry/Entity Type

Sports Bar

Font styles to use
Sans Serif

Colors

Designer to choose colors to be used in the design.

Requirements
Must have
• Logo, highlighted event schedule (beer pong Monday, trivia Tuesday, taco Tuesday, whiskey Wednesday, karaoke Saturday). The menu should be easy to read in a darkened bar. We'll be printing on standard 8.5x11 in portrait.
Nice to have
• We're trying to have the menu take up as few pages as possible.
Should not have
• We're trying to have the menu take up as few pages as possible. Food photography isn't necessary. A cover isn't necessary. Please avoid clip art of food.

```html
<!DOCTYPE html>
<html lang="en">
<head>
<meta charset="utf-8">
<title>Tinker's Lamp Menu</title>
<link rel="stylesheet" href="https://fonts.googleapis.com/css2?family=Montserrat:wght@600;700&family=Crimson+Text:wght@400;600&display=swap">
<style>
  :root {
    --page: #e4e4e4;
    --board-top: #35322f;
    --board-mid: #3b3936;
    --board-low: #2c2b2b;
    --ribbon: #f7ab34;
    --ink-dark: #1d1d1d;
    --accent: #f5a933;
    --white: #ffffff;
    --rule: #a7a7a7;
    --band: #8d6a30;
    --chip: #4f3e21;
    --chip-ink: #f1ddb2;
    --icon: #f3b548;
  }
  * { box-sizing: border-box; margin: 0; padding: 0; }
  html, body { width: 1200px; height: 1200px; overflow: hidden; }
  body { background: var(--page); font-family: "Crimson Text", Georgia, serif; }

  .menu {
    position: absolute; left: 190px; top: 20px;
    width: 820px; height: 1160px; overflow: hidden;
  }
  .menu__backdrop {
    position: absolute; inset: 0;
    background: radial-gradient(ellipse at 60% 35%, var(--board-mid) 0%, var(--board-top) 45%, var(--board-low) 100%);
  }

  .ribbon {
    position: absolute; left: 34px; top: 0; width: 100px; height: 195px;
    background: var(--ribbon);
    clip-path: polygon(0 0, 100% 0, 100% 100%, 50% 91%, 0 100%);
    display: flex; flex-direction: column; align-items: center; padding-top: 26px;
    font-size: 29px; line-height: 34px; color: var(--ink-dark); letter-spacing: 1px;
  }

  .brand {
    position: absolute; left: 240px; top: 48px; width: 400px;
    display: flex; flex-direction: column; align-items: center;
  }
  .brand__row { display: flex; align-items: center; gap: 12px; }
  .brand__mark { width: 18px; height: 18px; border-radius: 50%; background: var(--accent); }
  .brand__name {
    font-family: "Montserrat", Arial, sans-serif; font-weight: 700;
    font-size: 40px; color: var(--ink-dark);
  }
  .brand__tag {
    margin-top: 2px; font-size: 11px; letter-spacing: 6px; color: var(--ink-dark);
  }

  .panel {
    position: absolute;
    border: 2px solid var(--rule); border-top: none;
    display: flex; flex-direction: column; justify-content: space-between;
    padding: 28px 18px 20px 20px;
  }
  .panel__title {
    position: absolute; left: -2px; right: -2px; top: -11px;
    display: flex; align-items: center; gap: 6px;
    font-family: "Montserrat", Arial, sans-serif; font-weight: 700;
    font-size: 17px; color: var(--accent); white-space: nowrap;
  }
  .panel__title::before { content: ""; width: 12px; height: 2px; background: var(--rule); align-self: flex-start; margin-top: 10px; }
  .panel__title::after { content: ""; flex: 1; height: 2px; background: var(--rule); align-self: flex-start; margin-top: 10px; }
  .panel--burgers { left: 34px; top: 246px; width: 364px; height: 734px; }
  .panel--bites { left: 428px; top: 246px; width: 364px; height: 342px; padding-bottom: 26px; }
  .panel--flat { left: 428px; top: 636px; width: 364px; height: 343px; padding-bottom: 20px; }

  .dish__name {
    font-family: "Montserrat", Arial, sans-serif; font-weight: 700;
    font-size: 16.5px; line-height: 19px; color: var(--white);
  }
  .dish__desc { font-size: 12px; line-height: 17px; color: var(--accent); }
  .panel--bites .dish__desc, .panel--flat .dish__desc { line-height: 15px; }

  .events {
    position: absolute; left: 0; top: 1008px; width: 820px; height: 152px;
    background: var(--band);
  }
  .events__title {
    position: absolute; top: 14px; width: 100%; text-align: center;
    font-size: 21px; letter-spacing: 0.5px; color: var(--white);
  }
  .events__list { position: absolute; left: 39px; top: 48px; display: flex; gap: 29px; list-style: none; }
  .event {
    width: 125px; height: 81px; background: var(--chip);
    display: flex; flex-direction: column; align-items: center; justify-content: space-between;
    padding: 2px 0 4px;
  }
  .event__day { font-size: 16px; color: var(--white); line-height: 20px; }
  .event__icon { width: 36px; height: 32px; }
  .event__name { font-size: 14px; color: var(--chip-ink); line-height: 16px; }
</style>
</head>
<body>
<main class="menu">
  <div class="menu__backdrop" role="img" aria-label="Dim photograph of the pub's bar interior with shelves of bottles and hanging lamps"></div>

  <div class="ribbon" aria-label="Menu"><span>M</span><span>E</span><span>N</span><span>U</span></div>

  <header class="brand">
    <div class="brand__row"><span class="brand__mark"></span><span class="brand__name">Tinker's Lamp</span></div>
    <div class="brand__tag">PUB &amp; RESTAURANT</div>
  </header>

  <section class="panel panel--burgers">
    <h2 class="panel__title">BURGERS AND SANDWICHES</h2>
    <div class="dish"><h3 class="dish__name">Chicken Sandwich...$12</h3><p class="dish__desc">Chicken Breast, Applewood Bacon, Butter Lettuce, White Cheddar, Avocado and Tomato Served on Sourdough Bread</p></div>
    <div class="dish"><h3 class="dish__name">Buttermilk Fried Chicken...$13</h3><p class="dish__desc">Coleslaw, Provolone, Tomato, and a Spiced Mayonnaise on a Pretzel Roll</p></div>
    <div class="dish"><h3 class="dish__name">Short Rib Sandwich...$13</h3><p class="dish__desc">Beef Shorts, Mayo, Tomato, Caramelized Onions, Arugula, Pepper Jack Cheese Served on Sourdough Bread</p></div>
    <div class="dish"><h3 class="dish__name">Grilled Cheese Sandwich...$10</h3><p class="dish__desc">Cheese, Provolone and Cheddar Cheese</p></div>
    <div class="dish"><h3 class="dish__name">Tinker's Lamp Burger...$14</h3><p class="dish__desc">Sharp Cheddar, Arugula, Roasted Shallots, Bacon Jam with Malt Aioli</p></div>
    <div class="dish"><h3 class="dish__name">The Truffle Burger...$15</h3><p class="dish__desc">Caramelized Onions, Arugula, Truffle Pecorino, Truffle Mayo and Truffle Fries</p></div>
    <div class="dish"><h3 class="dish__name">The Sloppy Joe..$10</h3><p class="dish__desc">Shredded Lettuce and Sharp Cheddar</p></div>
    <div class="dish"><h3 class="dish__name">Veggie Burger...$12</h3><p class="dish__desc">Concoction of kale, Tomato, Avocado, Sharp Cheddar with a Balsamic Reduction</p></div>
    <div class="dish"><h3 class="dish__name">Flat Iron Steak Sandwich...$16</h3><p class="dish__desc">Arugula, Peppers, Fontina, Onion and Mayo</p></div>
    <div class="dish"><h3 class="dish__name">Chicken Spinach Wrap...$10</h3><p class="dish__desc">Chicken, Bacon, Lettuce, Tomato, Avocado, Ranch and Mayo</p></div>
    <div class="dish"><h3 class="dish__name">Fried Chicken Sliders (4)...$12</h3><p class="dish__desc">Coleslaw, Lime Sriracha Sauce</p></div>
  </section>

  <section class="panel panel--bites">
    <h2 class="panel__title">Big Dog Bites</h2>
    <div class="dish"><h3 class="dish__name">Atlantic Cod Fish N' Chips...$15</h3><p class="dish__desc">House Tartar Sauce, Vinegar and Lemon Wedge</p></div>
    <div class="dish"><h3 class="dish__name">Oven Roasted ½ Roasted Chicken...$16</h3><p class="dish__desc">Boneless Chicken, Broccolini, Fingerling Potatoes, Topped with Chimichurri Sauce</p></div>
    <div class="dish"><h3 class="dish__name">Black Mussels...$17</h3><p class="dish__desc">Tequila Chipotle Sauce, Cilantro and Cherry Tomatoes</p></div>
    <div class="dish"><h3 class="dish__name">Pan Seared Salmon...$19</h3><p class="dish__desc">Sushi Grade Salmon, Spaghetti Squash, Zucchini, Cherry Tomatoes In a Lemon Caper Beurre Blanc</p></div>
    <div class="dish"><h3 class="dish__name">Flat Iron Steak...$22</h3><p class="dish__desc">French Fries, Baby Arugula in a Light peppercorn Sauce</p></div>
  </section>

  <section class="panel panel--flat">
    <h2 class="panel__title">FlatBreads</h2>
    <div class="dish"><h3 class="dish__name">Margherita...$12</h3><p class="dish__desc">Fresh Mozzarella, Roma Tomatoes and Fresh Italian Basil</p></div>
    <div class="dish"><h3 class="dish__name">Vegetarian...$13</h3><p class="dish__desc">Brussel Sprouts, Peppers, Onions, Zucchini, Goat Cheese, Smoked Mozzarella Topped with a Balsamic Reduction</p></div>
    <div class="dish"><h3 class="dish__name">Prosciutto &amp; Arugula..$14</h3><p class="dish__desc">Red Onion, Parmesan, Mozzarella</p></div>
    <div class="dish"><h3 class="dish__name">Portobello &amp; Truffle...$14</h3><p class="dish__desc">Portobello White Mushroom, Fontina, Drizzled with Truffle Oil</p></div>
    <div class="dish"><h3 class="dish__name">Chicken Tikka Masala...$14</h3><p class="dish__desc">Tandoori Chicken, Fontini and Raita</p></div>
    <div class="dish"><h3 class="dish__name">The Tinker's Lamp...$15</h3><p class="dish__desc">Meatballs, Sausage, Chorizo, Mozzarella and Fresen</p></div>
  </section>

  <section class="events">
    <h2 class="events__title">EVENT SCHEDULE</h2>
    <ul class="events__list">
      <li class="event"><span class="event__day">Monday</span>
        <svg class="event__icon" viewBox="0 0 36 32" fill="none" stroke="var(--icon)" stroke-width="1.6"><circle cx="18" cy="16" r="14"/><circle cx="18" cy="16" r="10"/><line x1="10" y1="16" x2="26" y2="16"/></svg>
        <span class="event__name">Beer Pong</span></li>
      <li class="event"><span class="event__day">Tuesday</span>
        <svg class="event__icon" viewBox="0 0 36 32" fill="none" stroke="var(--icon)" stroke-width="1.6"><circle cx="18" cy="13" r="11"/><path d="M13 8h10v5a5 5 0 0 1-10 0z"/><line x1="18" y1="18" x2="18" y2="22"/><path d="M6 25h24l-2 5H8z"/></svg>
        <span class="event__name">Trivia</span></li>
      <li class="event"><span class="event__day">Wednesday</span>
        <svg class="event__icon" viewBox="0 0 36 32" fill="none" stroke="var(--icon)" stroke-width="1.6"><path d="M9 14h8v14H9z"/><path d="M19 14h8v14h-8z"/><line x1="18" y1="2" x2="18" y2="8"/><line x1="10" y1="4" x2="13" y2="9"/><line x1="26" y1="4" x2="23" y2="9"/></svg>
        <span class="event__name">Taco</span></li>
      <li class="event"><span class="event__day">Thursday</span>
        <svg class="event__icon" viewBox="0 0 36 32" fill="none" stroke="var(--icon)" stroke-width="1.6"><path d="M7 5h22l-11 13z"/><line x1="18" y1="18" x2="18" y2="28"/><line x1="12" y1="29" x2="24" y2="29"/><circle cx="27" cy="6" r="4"/></svg>
        <span class="event__name">Whiskey</span></li>
      <li class="event"><span class="event__day">Friday</span>
        <svg class="event__icon" viewBox="0 0 36 32" fill="none" stroke="var(--icon)" stroke-width="1.6"><circle cx="25" cy="9" r="6"/><line x1="20" y1="13" x2="7" y2="27"/><line x1="17" y1="11" x2="22" y2="16"/></svg>
        <span class="event__name">Karaoke</span></li>
    </ul>
  </section>
</main>
</body>
</html>
```